Garlic Farm for Farm Sales/Restaurant sales

Need a professional, but appealing to agriculture world. We are selling 27 kinds of Organic Garlic from a farm in Simla,CO. I have uploaded logo and business information-we are going to need a template, because I will need to use it for four separate people.
-We are trying to appeal to Farm to table restaurants
-As well as growers/farmers

Target Market(s)

Agriculture Sales/Restaurants-Organic

Industry/Entity Type

Agriculture

Contact Information for Business Card

Want it to look more unique then your average kelto stock card- I want it to look amazing

Font styles to use
Sans Serif

Colors
0455a3
ec1f27
fbed22
ffffff

Requirements
Must have
• Just be creative
Nice to have
• Colorful
Should not have
• plain

```html
<!DOCTYPE html>
<html lang="en">
<head>
<meta charset="utf-8">
<title>Prairie Crest Garlic – Business Card</title>
<link rel="stylesheet" href="https://fonts.googleapis.com/css2?family=Source+Sans+3:wght@400;600;700&display=swap">
<style>
  :root{
    --page:#d9d6d1;
    --navy-deep:#121a35;
    --navy:#24386a;
    --gold:#f0b51e;
    --red:#b3202c;
    --frost:#eceef0;
    --frost-edge:#dfe2e6;
    --ink:#1b2444;
    --white:#ffffff;
  }
  *{margin:0;padding:0;box-sizing:border-box}
  html,body{width:1200px;height:969px;overflow:hidden;background:var(--page)}
  body{position:relative;font-family:"Source Sans 3",sans-serif}
  .card{position:absolute;left:100px;top:200px;width:1000px;height:569px;overflow:hidden;
        background:linear-gradient(135deg,var(--frost),var(--frost-edge));
        box-shadow:0 18px 40px rgba(0,0,0,.25)}
  .card-art{position:absolute;inset:0;width:100%;height:100%}
  .line{position:absolute;left:48px;color:var(--white);font-size:24px;line-height:28px;white-space:nowrap}
  .holder-name{top:115px;font-size:32px;line-height:36px;font-weight:600;color:var(--gold);letter-spacing:.5px}
  .holder-title{top:162px}
  .addr-1{top:215px}
  .addr-2{top:253px}
  .contact{left:88px}
  .phone{top:305px}
  .email{top:343px}
  .web{top:381px}
  .contact-icon{position:absolute;left:56px;width:24px;height:24px}
  .brand{position:absolute;left:520px;top:338px;width:440px;text-align:center;
         font-size:44px;line-height:48px;font-weight:700;color:var(--ink)}
</style>
</head>
<body>
  <div class="card">
    <svg class="card-art" viewBox="0 0 580 330" preserveAspectRatio="none" aria-hidden="true">
      <defs>
        <linearGradient id="panelShade" x1="0" y1="0" x2="1" y2="0.4">
          <stop offset="0" stop-color="#1c2a52"/>
          <stop offset="0.6" stop-color="#26396b"/>
          <stop offset="1" stop-color="#121a35"/>
        </linearGradient>
      </defs>
      <path d="M0 0 H365 A200 200 0 0 0 365 330 H0 Z" fill="url(#panelShade)"/>
      <path d="M375 0 A205 205 0 0 0 290 262" fill="none" stroke="var(--gold)" stroke-width="4.5"/>
      <path d="M395 12 A195 195 0 0 0 360 330" fill="none" stroke="var(--red)" stroke-width="3"/>
      <g class="social-dots" fill="var(--gold)">
        <circle cx="38" cy="263" r="9"/>
        <circle cx="63" cy="263" r="9"/>
        <circle cx="88" cy="263" r="9"/>
        <circle cx="113" cy="263" r="9"/>
      </g>
      <circle class="brand-dot" cx="410" cy="125" r="33" fill="var(--red)"/>
    </svg>

    <div class="line holder-name">NORA ELLISON</div>
    <div class="line holder-title">CEO/FOUNDER</div>
    <div class="line addr-1">P.O. Box 12</div>
    <div class="line addr-2">Alder Flats, CO&nbsp; 80412</div>

    <svg class="contact-icon" style="top:307px" viewBox="0 0 24 24" aria-hidden="true">
      <path d="M6.6 10.8a15 15 0 0 0 6.6 6.6l2.2-2.2a1 1 0 0 1 1-.25 11.4 11.4 0 0 0 3.6.6 1 1 0 0 1 1 1V20a1 1 0 0 1-1 1A17 17 0 0 1 3 4a1 1 0 0 1 1-1h3.5a1 1 0 0 1 1 1c0 1.25.2 2.45.6 3.6a1 1 0 0 1-.25 1z" fill="var(--gold)"/>
    </svg>
    <div class="line contact phone">555-214-0937</div>

    <svg class="contact-icon" style="top:345px" viewBox="0 0 24 24" aria-hidden="true">
      <rect x="2" y="5" width="20" height="14" rx="1" fill="var(--gold)"/>
      <path d="M2.5 5.5 12 13l9.5-7.5" fill="none" stroke="var(--navy-deep)" stroke-width="1.6"/>
    </svg>
    <div class="line contact email">Nora@PCGarlic.com</div>

    <svg class="contact-icon" style="top:383px" viewBox="0 0 24 24" aria-hidden="true">
      <circle cx="12" cy="12" r="9.5" fill="none" stroke="var(--gold)" stroke-width="2"/>
      <ellipse cx="12" cy="12" rx="4" ry="9.5" fill="none" stroke="var(--gold)" stroke-width="1.6"/>
      <path d="M2.5 12h19M4 7h16M4 17h16" stroke="var(--gold)" stroke-width="1.4"/>
    </svg>
    <div class="line contact web">www.PCGarlic.com</div>

    <div class="brand">Prairie Crest Garlic</div>
  </div>
</body>
</html>
```